Storm Restoration Contractor needs a professional letterhead design

Looking for a professional letterhead design. Not looking for your cheapo MS Word standard ones that are readily available. Dont want it to be cookie cutter look like ones readily available online. We just recently changed our logo and want to freshen up all our documents. Our company handles restoring a property back to a pre-loss condition after a storm damages it. For example, wind, hail, flood, fire losses.

Target Market(s)

Property Owners, Homeowners, Property Owners, Commercial Property Owners, Property Management Companies

Industry/Entity Type

Construction Company

Requirements
Must have
• Professional, Use 1 of 2 logo options
• Storm Restoration, Roofing, Siding, Windows

```html
<!DOCTYPE html>
<html lang="en">
<head>
<meta charset="utf-8">
<title>Northgate Exteriors — Letterhead &amp; Folder</title>
<link rel="stylesheet" href="https://fonts.googleapis.com/css2?family=Questrial&family=Lato:wght@400;700&display=swap">
<style>
  :root {
    --bg: #e9ecee;
    --paper: #ffffff;
    --folder: #dcdcdc;
    --blue: #1f7bc4;
    --charcoal: #4d4d4f;
    --ink: #2b2b2b;
    --muted: #555;
    --wash: rgba(31,123,196,0.10);
  }
  * { margin: 0; padding: 0; box-sizing: border-box; }
  html, body { width: 1200px; height: 784px; overflow: hidden; }
  body { background: var(--bg); font-family: "Questrial", sans-serif; color: var(--ink); position: relative; }

  .letterhead {
    position: absolute; left: 42px; top: 45px; width: 514px; height: 697px;
    background: var(--paper); border-radius: 10px; overflow: hidden;
  }
  .letterhead .bands { position: absolute; left: 0; top: 0; }
  .watermark {
    position: absolute; left: 135px; top: 218px; width: 250px; height: 250px;
    border: 26px solid var(--wash); border-radius: 50%;
  }
  .brand {
    position: absolute; left: 0; right: 0; top: 48px;
    display: flex; flex-direction: column; align-items: center; gap: 10px;
  }
  .brand-dot { width: 64px; height: 64px; border-radius: 50%; border: 7px solid var(--blue); }
  .brand-name { font-size: 13px; letter-spacing: 1.2px; color: var(--blue); text-transform: uppercase; }

  .body-copy {
    position: absolute; left: 48px; top: 140px; width: 424px;
    font-size: 11.2px; line-height: 17.6px; text-align: justify; color: var(--ink);
  }
  .body-copy p + p { margin-top: 17.6px; }

  .signature { position: absolute; left: 384px; top: 580px; }
  .signature .name { font-size: 14px; color: var(--ink); }
  .signature .role { font-size: 10px; color: var(--muted); margin-top: 9px; }

  .contact {
    position: absolute; left: 48px; top: 614px;
    font-family: "Lato", sans-serif; font-size: 6.6px; color: var(--muted); line-height: 13.5px;
  }
  .contact li { list-style: none; display: flex; align-items: center; gap: 4px; }
  .contact svg { width: 7px; height: 7px; fill: var(--blue); }
  .contact .address { font-weight: 700; color: var(--ink); margin-top: 1px; }

  .website {
    position: absolute; left: 26px; bottom: 6px;
    font-family: "Lato", sans-serif; font-size: 8px; letter-spacing: 2.2px; color: #fff;
  }

  .folder {
    position: absolute; left: 634px; top: 45px; width: 513px; height: 697px;
    background: var(--folder); border-radius: 10px;
  }
  .folder-brand {
    position: absolute; left: 130px; top: 565px; display: flex; align-items: center; gap: 14px;
  }
  .folder-brand .brand-dot { width: 44px; height: 44px; border-width: 5px; }
  .folder-brand .rule { width: 2px; height: 72px; background: var(--blue); }
  .folder-brand .brand-name { font-size: 26px; line-height: 29px; letter-spacing: 1px; }
</style>
</head>
<body>

<section class="letterhead">
  <svg class="bands" width="514" height="697" viewBox="0 0 514 697" aria-hidden="true">
    <polygon points="0,0 372,0 364,6 0,6" fill="var(--charcoal)"/>
    <polygon points="372,0 514,0 514,14 356,14" fill="var(--blue)"/>
    <polygon points="228,683 514,683 514,697 214,697" fill="var(--charcoal)"/>
    <polygon points="0,671 240,671 204,697 0,697" fill="var(--blue)"/>
  </svg>

  <div class="watermark" aria-hidden="true"></div>

  <header class="brand">
    <div class="brand-dot" aria-hidden="true"></div>
    <div class="brand-name">Northgate Exteriors</div>
  </header>

  <div class="body-copy">
    <p>Lorem ipsum dolor sit amet, consectetur adipiscing elit. Donec orci purus, luctus vitae dignissim eu, iaculis sed purus. Vivamus faucibus, ipsum nec aliquet viverra, leo mauris condimentum ligula, sit amet sagittis enim ligula quis arcu. Nam egestas tortor id nisi porttitor mattis. In tortor ante, ultricies in suscipit a, tempus non massa. Vivamus et auctor mi. Fusce vel massa nulla. Phasellus nec eros mauris, et scelerisque orci. Donec malesuada orci vitae nulla accumsan porta a id massa.</p>
    <p>Quisque accumsan iaculis magna sit amet fringilla. Maecenas consequat, magna eget tincidunt semper, odio nibh rutrum mi, id feugiat ante nisi eu risus. Vestibulum nunc orci, rhoncus a placerat in, ultricies in mi. Cras mattis varius eros, vel fringilla nisi suscipit eget. Quisque scelerisque sagittis nulla at porttitor. Mauris a justo et tellus interdum tristique. Sed id augue vitae urna euismod commodo aliquet a quam. Pellentesque arcu velit, cursus et malesuada ut, consequat et diam. Nullam erat sem, rhoncus id ullamcorper vitae, rhoncus et arcu. In ultricies ultricies nulla,</p>
    <p>Kut rutrum nisi iaculis at. Donec eu magna a metus ornare faucibus. Fusce aliquet faucibus ultricies. Morbi semper, est id tincidunt gravida, sem arcu adipiscing lacus, ac bibendum nulla leo eu purus. Quisque nec diam sed risus consectetur a ccumsan quis quis nibh. Vestibulum id purus lorem. Donec eu magna a metus ornare faucibus. Fusce aliquet faucibus ultricies. Morbi semper, est id tincidunt gravida, sem arcu adipiscing lacus, ac bibendum nulla leo eu purus. Quisque nec diam sed risus consectetur a ccumsan quis quis nibh. Vestibulum id purus lorem.</p>
  </div>

  <div class="signature">
    <div class="name">Dale Harmon</div>
    <div class="role">Co-Founder &amp; CEO</div>
  </div>

  <ul class="contact">
    <li><svg viewBox="0 0 10 10"><path d="M2 0h2l1 3-1.5 1a6 6 0 0 0 2.5 2.5L7 5l3 1v2a2 2 0 0 1-2 2A8 8 0 0 1 0 2a2 2 0 0 1 2-2z"/></svg>(555) 014-2290</li>
    <li><svg viewBox="0 0 10 10"><rect x="2" y="0" width="6" height="3"/><rect x="0" y="3.5" width="10" height="4" rx="1"/><rect x="2" y="7" width="6" height="3"/></svg>(555) 014-3381</li>
    <li><svg viewBox="0 0 10 10"><path d="M0 1.5h10v7H0z M0 1.5l5 4 5-4" /></svg>info@northgateexteriors.com</li>
    <li class="address">480 Meadow Ridge Drive, 2nd Floor, Fairview, GA 30000</li>
  </ul>

  <div class="website">www.northgateexteriors.com</div>
</section>

<section class="folder">
  <div class="folder-brand">
    <div class="brand-dot" aria-hidden="true"></div>
    <div class="rule" aria-hidden="true"></div>
    <div class="brand-name">Northgate<br>Exteriors</div>
  </div>
</section>

</body>
</html>
```